A business card design for a dental office. We have Two doctors working here. We practice general de

I already have a logo designed for the office with the name and a slogan.
Now I need to create design for a business card using the same logo.
Details Needed on the front side of the card are :
Bernard K. Oswin, DDS
Gerald M Fenwick, DDS
418 Birch Lane
Elmfield, VT 00000
Phone : 555 019 4831
Fax : 555 019 4832
Website : WWW.BrightmoorToothHaven.Com
Office hours by appointment
On the back side of the card need :
Appointment
Date....................Time...................
With....................................
If unable to keep your appointment, please give 24-48 hours notice in order to avoid broken appointment fee.

Industry/Entity Type

Dental Clinic

Contact Information for Business Card

Bernard K. Oswin, DDS
Gerald M Fenwick, DDS
418 Birch Lane
Elmfield, VT 00000
Phone : 555 019 4831
Fax : 555 019 4832
Appointment

Requirements
Must have
• Keep the Name and slogan on the logo on the front of the card. You can move them around the Logo and Name/Slogan of business (Oswin Family Dentistry/We give you reasons to smile) as you wish to get a feel of the design.
• Bernard K. Oswin, DDS
• Gerald M Fenwick, DDS
• 418 Birch Lane
• Elmfield, VT 00000
• Phone : 555 019 4831
• Fax : 555 019 4832
• WWW.BrightmoorToothHaven.Com
• Keep these three groups above as they are together now in different areas of the front side.
• On the back side of the card need :
• Appointment
• Date....................Time...................
• With....................................
• If unable to keep your appointment, please give 24-48 hours notice in order to avoid broken appointment fee.

```html
<!DOCTYPE html>
<html lang="en">
<head>
<meta charset="utf-8">
<title>Oswin Family Dentistry – Business Card</title>
<link href="https://fonts.googleapis.com/css2?family=Arimo:wght@400&family=Cinzel:wght@700&family=Exo+2:wght@700&display=swap" rel="stylesheet">
<style>
  :root {
    --backdrop: #e9e6e1;
    --card-white: #ffffff;
    --brand-blue: #1c4f9c;
    --deep-blue: #0d4a8a;
    --grad-left: #0a5ba8;
    --grad-right: #6aa6d9;
    --accent-green: #1aa886;
    --accent-red: #d8261f;
    --logo-circle: #3f86c9;
    --ink: #111111;
  }
  * { margin: 0; padding: 0; box-sizing: border-box; }
  html, body { width: 1189px; height: 1200px; overflow: hidden; background: var(--backdrop); }
  .card {
    position: absolute; left: 140px; width: 917px;
    background: var(--card-white); overflow: hidden;
    box-shadow: 0 6px 14px rgba(0,0,0,.25);
  }
  .card-front { top: 45px; height: 524px; }
  .card-back { top: 624px; height: 523px; }
  .card-bg { position: absolute; inset: 0; width: 100%; height: 100%; }

  .logo-mark { position: absolute; left: 96px; top: 24px; width: 164px; height: 164px; border-radius: 50%; background: var(--logo-circle); }
  .practice-name {
    position: absolute; left: 292px; top: 84px; width: 570px;
    font-family: "Exo 2", sans-serif; font-weight: 700; font-size: 38px; line-height: 44px;
    color: var(--brand-blue); letter-spacing: 4px; text-transform: uppercase; white-space: nowrap;
  }
  .slogan {
    position: absolute; left: 292px; top: 138px; width: 565px;
    display: flex; align-items: center; justify-content: center; gap: 12px;
    font-family: "Exo 2", sans-serif; font-weight: 700; font-size: 15px;
    color: var(--accent-red); letter-spacing: 3.5px; text-transform: uppercase; white-space: nowrap;
  }
  .slogan::before, .slogan::after { content: ""; width: 42px; height: 1px; background: var(--accent-red); }

  .doctors { position: absolute; left: 46px; top: 348px; color: #fff; font-family: "Cinzel", serif; font-weight: 700; }
  .doctor-name { font-size: 32px; line-height: 34px; letter-spacing: .5px; white-space: nowrap; }
  .doctor-title { font-size: 24px; line-height: 26px; margin-bottom: 10px; }

  .divider { position: absolute; left: 413px; top: 318px; width: 3px; height: 180px; background: #fff; }
  .contacts { position: absolute; left: 434px; top: 332px; list-style: none; color: #fff; font-family: "Arimo", sans-serif; font-size: 26px; }
  .contacts li { display: flex; align-items: center; gap: 10px; height: 40.5px; white-space: nowrap; }
  .contacts svg { width: 16px; height: 16px; flex: none; }

  .appointment-title {
    position: absolute; left: 0; right: 0; top: 24px; text-align: center;
    font-family: "Cinzel", serif; font-weight: 700; font-size: 63px; line-height: 72px; color: #fff; letter-spacing: 1px;
  }
  .appointment-lines { position: absolute; left: 65px; top: 242px; width: 800px; font-family: "Arimo", sans-serif; font-size: 30px; line-height: 36px; color: var(--ink); }
  .appointment-lines p { height: 71px; white-space: nowrap; overflow: hidden; }
</style>
</head>
<body>

<section class="card card-front" aria-label="Card front">
  <svg class="card-bg" viewBox="0 0 917 524" preserveAspectRatio="none" aria-hidden="true">
    <defs>
      <linearGradient id="front-blue" x1="0" y1="1" x2="1" y2="0">
        <stop offset="0" stop-color="var(--grad-left)"/>
        <stop offset="1" stop-color="var(--grad-right)"/>
      </linearGradient>
    </defs>
    <path d="M0 175 C 245 345, 655 345, 917 171 L917 524 L0 524 Z" fill="url(#front-blue)"/>
    <path d="M33 188 C 270 345, 645 345, 878 188" fill="none" stroke="#fff" stroke-width="18"/>
    <path d="M36 183 C 270 335, 645 335, 875 184" fill="none" stroke="var(--accent-green)" stroke-width="10"/>
  </svg>

  <div class="logo-mark" aria-hidden="true"></div>
  <h1 class="practice-name">Oswin Family Dentistry</h1>
  <p class="slogan">We give you reasons to smile</p>

  <div class="doctors">
    <p class="doctor-name">Bernard K. Oswin</p>
    <p class="doctor-title">DDS</p>
    <p class="doctor-name">Gerald M Fenwick</p>
    <p class="doctor-title">DDS</p>
  </div>

  <div class="divider" aria-hidden="true"></div>

  <ul class="contacts">
    <li>
      <svg viewBox="0 0 16 16" aria-hidden="true"><rect width="16" height="16" rx="2" fill="#fff"/><path d="M5 3 L7 5 L6 7 Q7 9.5 9 10 L11 9 L13 11 L11.5 13 Q5 12 3 5 Z" fill="var(--grad-left)"/></svg>
      <span>555 019 4831</span>
    </li>
    <li>
      <svg viewBox="0 0 16 16" aria-hidden="true"><rect width="16" height="16" rx="2" fill="#fff"/><rect x="3" y="5" width="10" height="7" fill="var(--grad-left)"/><rect x="5" y="3" width="6" height="3" fill="var(--grad-left)"/><rect x="5" y="8" width="6" height="1.5" fill="#fff"/></svg>
      <span>555 019 4832</span>
    </li>
    <li>
      <svg viewBox="0 0 16 16" aria-hidden="true"><rect width="16" height="16" rx="2" fill="#fff"/><circle cx="8" cy="8" r="5" fill="none" stroke="var(--grad-left)" stroke-width="1.6"/><path d="M3 8 H13 M8 3 Q5 8 8 13 Q11 8 8 3" fill="none" stroke="var(--grad-left)" stroke-width="1.2"/></svg>
      <span>WWW.BrightmoorToothHaven.Com</span>
    </li>
    <li>
      <svg viewBox="0 0 16 16" aria-hidden="true"><rect width="16" height="16" rx="2" fill="#fff"/><path d="M8 3 A3.5 3.5 0 0 1 11.5 6.5 Q11.5 9 8 13 Q4.5 9 4.5 6.5 A3.5 3.5 0 0 1 8 3 Z" fill="var(--grad-left)"/><circle cx="8" cy="6.5" r="1.3" fill="#fff"/></svg>
      <span>418 Birch Lane Elmfield, VT 00000</span>
    </li>
  </ul>
</section>

<section class="card card-back" aria-label="Card back">
  <svg class="card-bg" viewBox="0 0 917 523" preserveAspectRatio="none" aria-hidden="true">
    <path d="M0 0 H917 V122 Q458 50 0 157 Z" fill="var(--deep-blue)"/>
    <path d="M0 160 Q458 55 917 124" fill="none" stroke="var(--accent-red)" stroke-width="5"/>
  </svg>

  <h2 class="appointment-title">Appointment</h2>

  <div class="appointment-lines">
    <p>Date...................Time..................With.....................................</p>
    <p>Date...................Time..................With.....................................</p>
    <p>Date...................Time..................With.....................................</p>
  </div>
</section>

</body>
</html>
```